Halvern Studio Works New Business Card

I am opening a new division of my business. I am a high end interior designer, and the new business is writing specs for construction projects. It will be marketed to the VERY high end contractor, architects and realtors. The client will actually be the one who pays us and signs the agreement, but it will be the contractor, architect or realtor that will recommend us. I have attached my current card and our previous logo which is still used on some of our paperwork. I would like the new logo to be connected in some way to what we are currently using. We will need to have room on the card for a person's name. I'd like to omit the address as we might be moving the office soon. The web address is www.HalvernStudioWorks.com. For this design, please use my name, Marisol Thornbury.

Target Market(s)

High End Luxury Contractors, Realtors and Architects

Industry/Entity Type

Residential Construction

Contact Information for Business Card

Halvern Studio Works, Phone: 555-214-9087, www.HalvernStudioWorks.com , Marisol Thornbury

Font styles to use
Sans Serif

Colors
ec1f27

Requirements
Must have
• Some visual reference to my current card and logos. Use the colors submitted on the business card I attached.
Nice to have
• A visual reference to my current card and logos. Use the colors submitted on the card I attached.
Should not have
• A physical address

```html
<!DOCTYPE html>
<html lang="en">
<head>
<meta charset="utf-8">
<title>Halvern Studio Works – Business Card</title>
<link rel="stylesheet" href="https://fonts.googleapis.com/css2?family=Open+Sans:wght@400;700&family=Roboto+Condensed:wght@300&display=swap">
<style>
  :root {
    --backdrop: #e9e6e2;
    --card: #ffffff;
    --brand: #8a2a14;
    --brand-text: #7c2510;
    --body-text: #666666;
  }
  html, body {
    margin: 0;
    padding: 0;
    width: 1200px;
    height: 1000px;
    overflow: hidden;
    background: var(--backdrop);
  }
  .card {
    position: absolute;
    left: 100px;
    top: 202px;
    width: 1000px;
    height: 596px;
    background: var(--card);
    box-shadow: 0 4px 14px rgba(0,0,0,0.18);
  }
  .brand {
    position: absolute;
    left: 40px;
    top: 205px;
    width: 455px;
    text-align: center;
  }
  .brand-square {
    display: block;
    width: 94px;
    height: 94px;
    margin: 0 auto 14px;
    background: var(--brand);
  }
  .brand-name {
    margin: 0;
    font-family: "Roboto Condensed", "Arial Narrow", sans-serif;
    font-weight: 300;
    font-size: 52px;
    line-height: 1.1;
    color: var(--brand-text);
    white-space: nowrap;
  }
  .contact {
    position: absolute;
    left: 547px;
    top: 200px;
  }
  .person-name {
    margin: 0 0 46px;
    font-family: "Open Sans", sans-serif;
    font-weight: 700;
    font-size: 26px;
    letter-spacing: 0.2px;
    color: var(--brand-text);
    text-transform: uppercase;
  }
  .contact-list {
    list-style: none;
    margin: 0;
    padding: 0;
  }
  .contact-item {
    display: flex;
    align-items: center;
    gap: 10px;
    height: 36px;
    font-family: "Open Sans", sans-serif;
    font-size: 23px;
    color: var(--body-text);
  }
  .contact-icon {
    width: 20px;
    height: 20px;
    flex: none;
    fill: var(--brand);
  }
</style>
</head>
<body>
  <article class="card">
    <div class="brand">
      <span class="brand-square"></span>
      <p class="brand-name">Halvern Studio Works</p>
    </div>
    <div class="contact">
      <h1 class="person-name">Marisol Thornbury</h1>
      <ul class="contact-list">
        <li class="contact-item">
          <svg class="contact-icon" viewBox="0 0 20 20" aria-hidden="true">
            <path d="M2 7c0-2 3.5-3.5 8-3.5S18 5 18 7v1.5h-4V7H6v1.5H2z"/>
            <path d="M5 9.5h10l2 7H3z"/>
          </svg>
          <span>555-214-9087</span>
        </li>
        <li class="contact-item">
          <svg class="contact-icon" viewBox="0 0 20 20" aria-hidden="true">
            <path d="M2 4.5h16v11H2z M3.5 6l6.5 5 6.5-5v-.2h-13z" fill-rule="evenodd"/>
          </svg>
          <span>info@HalvernStudioWorks.com</span>
        </li>
        <li class="contact-item">
          <svg class="contact-icon" viewBox="0 0 20 20" aria-hidden="true">
            <path d="M2 3h16v11H2z M4 5v7h12V5z M8 15h4v1.5h3V18H5v-1.5h3z" fill-rule="evenodd"/>
          </svg>
          <span>www.HalvernStudioWorks.com</span>
        </li>
      </ul>
    </div>
  </article>
</body>
</html>
```